Business Card Design Project

We need a business card for a new technology services company. We develop software and implement software packages for our business customers and although we will begin with just one or two service offerings, our service offerings will expand over time. Our name comes from the an author, KL Barrow, and his "idea" was that opportunity should be based on ability and achievement, not on social status.

We would like to see a design that is standard in its size and shape, but stands apart in its dramatic color contrasts. The card should not use too many colors - the colors used in the background should highlight the brilliant blues of the logo (see attachment) to dramatic effect. The background should not be white.

If necessary, you can change the color of the words "KL Barrow", but not the word "Idea".

Card size should be U.S. standard 2 inches by 3.5 inches and provide for 1/8 inch bleed area on each side.

We need a design for both sides of the business card, one side communicating the company logo and contact information, the other side being purely graphical, incorporating the logo but no other information.

Contact Information Required:
Kate Brook
KateBrook@klbarrowvista.com
614-387-2259

Target Market(s)

Business executives

Industry/Entity Type

Software

Requirements
Must have
• It must have the full company logo on one side, and at least the graphic element of the logo on the other. Either that or the full logo on both.
Nice to have
• It would be nice to have a design that could work without needing two different textures. For example, it would be nice if the entire card could be shiny, not just parts of the card.

It would also be nice if texture is something we could add later.
Should not have
• The card should not use the color green.

```html
<!DOCTYPE html>
<html lang="en">
<head>
<meta charset="utf-8">
<title>Barrow Vista – Business Card</title>
<link rel="stylesheet" href="https://fonts.googleapis.com/css2?family=Roboto:wght@300&family=Cinzel:wght@500&family=Arimo:wght@400&display=swap">
<style>
  :root {
    --page: #e8e5e0;
    --card-dark: #1c1c1e;
    --card-mid: #3a3a3d;
    --brand-blue: #1e9bd7;
    --band-blue: #14a3e0;
    --silver: #a9abae;
    --white: #ffffff;
    --shadow: rgba(0, 0, 0, 0.28);
  }
  * { margin: 0; padding: 0; box-sizing: border-box; }
  html, body {
    width: 1200px;
    height: 750px;
    overflow: hidden;
    background: var(--page);
  }
  .canvas {
    position: relative;
    width: 1200px;
    height: 750px;
  }
  .card {
    position: absolute;
    top: 220px;
    width: 540px;
    height: 309px;
    overflow: hidden;
    background: linear-gradient(160deg, var(--card-mid) 0%, var(--card-dark) 55%, #111113 100%);
    box-shadow: 0 10px 28px var(--shadow);
  }
  .card--front { left: 40px; }
  .card--back { left: 620px; }

  /* Front */
  .card__band {
    position: absolute;
    inset: 0;
    width: 540px;
    height: 309px;
  }
  .brand {
    position: absolute;
    display: flex;
    align-items: center;
    gap: 14px;
  }
  .brand__dot {
    width: 22px;
    height: 22px;
    border-radius: 50%;
    background: var(--brand-blue);
  }
  .brand__name {
    font-family: "Roboto", Arial, sans-serif;
    font-weight: 300;
    color: var(--brand-blue);
    letter-spacing: -1px;
    white-space: nowrap;
  }
  .card--front .brand { left: 92px; top: 92px; }
  .card--front .brand__name { font-size: 46px; }

  .contact {
    position: absolute;
    left: 0;
    right: 0;
    top: 226px;
    color: var(--white);
    text-align: center;
  }
  .contact__name {
    font-family: "Cinzel", "Times New Roman", serif;
    font-weight: 500;
    font-size: 21px;
    letter-spacing: 1px;
    margin-left: 70px;
  }
  .contact__lines {
    display: flex;
    justify-content: center;
    gap: 22px;
    margin-top: 14px;
    margin-left: 90px;
    font-family: "Arimo", Arial, sans-serif;
    font-size: 13px;
  }
  .contact__item {
    display: flex;
    align-items: center;
    gap: 6px;
  }
  .contact__icon { width: 12px; height: 12px; }

  /* Back */
  .card__pattern {
    position: absolute;
    inset: 0;
    background: radial-gradient(ellipse at 55% 50%, rgba(30, 120, 170, 0.35) 0%, rgba(30, 110, 160, 0.18) 50%, rgba(0, 0, 0, 0) 85%);
  }
  .card--back .brand {
    right: 34px;
    top: 120px;
  }
  .card--back .brand__name { font-size: 66px; }
</style>
</head>
<body>
<main class="canvas">

  <section class="card card--front" aria-label="Business card front">
    <svg class="card__band" viewBox="0 0 540 309" aria-hidden="true">
      <path d="M0,262 Q220,150 540,158" fill="none" stroke="var(--silver)" stroke-width="5"/>
      <path d="M0,309 L0,276 Q230,166 540,170 L540,309 Z" fill="var(--band-blue)"/>
    </svg>
    <div class="brand">
      <span class="brand__dot" aria-hidden="true"></span>
      <span class="brand__name">Barrow Vista</span>
    </div>
    <div class="contact">
      <p class="contact__name">Kate Brook</p>
      <div class="contact__lines">
        <span class="contact__item">
          <svg class="contact__icon" viewBox="0 0 12 12" aria-hidden="true">
            <path d="M2.5,1 L4.5,1 L5.3,3.4 L4,4.3 Q5,6.9 7.7,8 L8.6,6.7 L11,7.5 L11,9.5 Q11,11 9.5,11 Q1,10.5 1,2.5 Q1,1 2.5,1 Z" fill="var(--white)"/>
          </svg>
          614-387-2259
        </span>
        <span class="contact__item">
          <svg class="contact__icon" viewBox="0 0 12 12" aria-hidden="true">
            <rect x="0.5" y="2.5" width="11" height="7.5" rx="1" fill="var(--white)"/>
            <path d="M1,3 L6,7 L11,3" fill="none" stroke="var(--band-blue)" stroke-width="1"/>
          </svg>
          KateBrook@klbarrowvista.com
        </span>
      </div>
    </div>
  </section>

  <section class="card card--back" aria-label="Business card back">
    <div class="card__pattern" role="img" aria-label="Faint repeating blue brand symbol pattern across the dark card"></div>
    <div class="brand">
      <span class="brand__name">Barrow Vista</span>
    </div>
  </section>

</main>
</body>
</html>
```